eCommerce website for a DIY shop & communal center

We need a website for a business called The Maple Bench. The Maple Bench is both a shop and communal establishment where people with shared interests, especially in DIY (Do It Yourself) and crafting, can gather to shop for & work on projects while sharing ideas, equipment, supplies and knowledge. The shop is both brick & motor and online. The physical communal space provides workstations, equipment, tools and supplies and expertise for DIY lovers to create their projects.

Target Market(s)

Middle & upper class DIY enthusiasts, creative hobbyists, budding artists & small business owners

Industry/Entity Type

DIY, Arts & Crafts

Coding

Coded - Design and coding required

Number of Pages Required

5+ page

Requirements
Must have
• Menus to include 1. home page (with about us, operating hours, contacts, location, meet the team); 2. Bench activities (how to DIY at the Bench, booking, equipment & tools, house rules); 3. Bench events (events in the Bench, offsite events); 4. Resources (FAQs, tutorials, blogs, eBooks) and 5. Online shop
Nice to have
• Branding guidelines eg logo colours (see attachment) to influence design. Tillpost shop. Booking feature for activities & events at the Bench.

```html
<!DOCTYPE html>
<html lang="en">
<head>
<meta charset="utf-8">
<title>The Maple Bench — DIY Shop &amp; Communal Workshop</title>
<link href="https://fonts.googleapis.com/css2?family=Rubik:wght@500;700;800&family=Roboto:wght@400;500;700&display=swap" rel="stylesheet">
<style>
:root{
  --purple:#2a0b8c;
  --purple-deep:#240a7a;
  --orange:#f7a034;
  --orange-soft:#f3c185;
  --ink:#111;
  --text:#555;
  --grey:#f0f0f0;
  --white:#fff;
}
*{box-sizing:border-box;margin:0;padding:0}
html,body{width:1200px;height:4743px;overflow:hidden}
body{position:relative;background:var(--white);font-family:Roboto,Arial,sans-serif;color:var(--text)}
.abs{position:absolute}
.heading{font-family:Rubik,Arial,sans-serif;font-weight:800;color:var(--ink);letter-spacing:.5px}
.brush{position:absolute;height:9px;background:var(--orange);border-radius:6px 3px 6px 3px;transform:skewX(-20deg)}
.btn{position:absolute;background:var(--purple);color:#fff;font:700 13px Roboto,sans-serif;display:flex;align-items:center;justify-content:center;gap:8px;border-radius:3px;letter-spacing:.2px}
.btn .dot{width:13px;height:13px;border-radius:50%;background:#fff;color:var(--purple);font-size:9px;display:flex;align-items:center;justify-content:center}
.photo{position:absolute}

/* header */
.site-header{position:absolute;left:0;top:0;width:1200px;height:80px;background:#fff}
.brand{position:absolute;left:108px;top:26px;display:flex;align-items:center;gap:8px;font:700 19px Rubik,sans-serif;color:var(--orange)}
.brand .mark{width:16px;height:16px;border-radius:50%;background:var(--orange)}
.main-nav{position:absolute;top:31px;left:322px;font:700 13px Roboto,sans-serif;color:var(--ink)}
.main-nav span{position:absolute;white-space:nowrap}
.main-nav .active{color:var(--orange)}

/* hero */
.hero-photo{left:0;top:80px;width:1200px;height:520px;background:linear-gradient(100deg,#8a6a55 0%,#c9a08a 25%,#e7d2c5 55%,#b9a5a0 75%,#6f6a8c 100%)}
.hero-frame{left:173px;top:228px;width:854px;height:262px;border:4px solid #fff;background:rgba(255,255,255,.72);text-align:center}
.hero-frame h1{font:800 33px Rubik,sans-serif;color:var(--purple);margin-top:52px;letter-spacing:.3px}
.hero-frame p{font-size:14px;line-height:22px;color:#666;margin:12px auto 0;width:640px}
.play{display:inline-flex;align-items:center;gap:8px;margin-top:24px;font:500 15px Roboto,sans-serif;color:var(--purple)}
.play i{width:13px;height:13px;border-radius:50%;background:var(--purple);display:inline-block}

/* about */
.about-text{left:115px;top:830px;width:450px;font-size:13.5px;line-height:25.8px;color:#666}

/* provide */
.provide-card{position:absolute;top:1375px;width:317px;height:245px}
.provide-card .label{position:absolute;left:0;top:170px;width:236px;height:40px;background:#fff;font:800 17px Rubik,sans-serif;color:var(--ink);display:flex;align-items:center;justify-content:center}
.arrow{position:absolute;width:38px;height:38px;border-radius:50%;background:#fff;box-shadow:0 1px 5px rgba(0,0,0,.2);display:flex;align-items:center;justify-content:center}

/* features */
.feature{position:absolute;top:2425px;width:230px;text-align:center;color:#fff}
.feature h3{font:700 13px Roboto,sans-serif;margin-top:22px;letter-spacing:.2px}
.feature .line{width:34px;height:2px;background:#fff;margin:14px auto 14px}
.feature p{font-size:13.5px;line-height:21px}

/* blog */
.blog-post{position:absolute;top:2873px;width:420px;text-align:center}
.blog-post h4{font:700 13px Roboto,sans-serif;color:var(--ink);line-height:22px;margin-top:28px}
.blog-post .meta{font-size:11px;color:#777;margin-top:12px}
.blog-post .meta b{color:var(--orange);font-weight:400}
.blog-post p{font-size:12.5px;line-height:19px;color:#666;margin-top:12px}

/* team */
.member{position:absolute;top:3525px;width:238px;height:270px;background:#fff;box-shadow:0 2px 8px rgba(0,0,0,.15)}
.member .face{position:absolute;left:6px;top:6px;width:226px;height:184px;background:linear-gradient(180deg,#6f6f6f,#4d4d4d)}
.member h5{position:absolute;top:213px;width:100%;text-align:center;font:700 12px Roboto,sans-serif;color:var(--ink)}
.socials{position:absolute;display:flex;gap:4px}
.socials i{width:24px;height:24px;border-radius:50%;border:1px solid var(--orange);display:block}

/* contact */
.contact-band{left:0;top:3870px;width:1200px;height:470px;background:linear-gradient(120deg,#f9a53a,#f69a2d 50%,#f8a942)}
.field{position:absolute;background:#fff;font-size:14px;color:#777;padding:15px 22px}

/* footer */
.site-footer{left:0;top:4335px;width:1200px;height:408px;background:var(--purple)}
.site-footer .col-title{position:absolute;font:700 13px Roboto,sans-serif;color:#fff}
.site-footer .col-title::after{content:"";position:absolute;left:0;top:26px;width:26px;height:2px;background:#fff}
.f-list{position:absolute;color:#fff;font-size:13.5px}
.f-list div{height:30.5px;white-space:nowrap}
.f-list div::before{content:"»";margin-right:16px}
.vline{position:absolute;top:4390px;width:1px;height:200px;background:rgba(255,255,255,.35)}
.c-item{position:absolute;left:603px;display:flex;gap:20px;color:#fff;font-size:12px;line-height:17px}
.c-item .ic{width:28px;height:28px;border:1px solid rgba(255,255,255,.7);flex:none;display:flex;align-items:center;justify-content:center}
</style>
</head>
<body>

<!-- Header -->
<header class="site-header">
  <div class="brand"><span class="mark"></span>THE MAPLE BENCH</div>
  <nav class="main-nav">
    <span class="active" style="left:0">HOME</span>
    <span style="left:74px">ABOUT US</span>
    <span style="left:176px">BENCH ACTIVITIES</span>
    <span style="left:340px">BENCH EVENTS</span>
    <span style="left:481px">RESOURCES</span>
  </nav>
  <div class="btn" style="left:932px;top:17px;width:155px;height:45px">ONLINE SHOP
    <svg width="14" height="12" viewBox="0 0 14 12"><path d="M0 1h3l2 7h7l2-5H4" fill="none" stroke="#fff" stroke-width="1.6"/><circle cx="6" cy="10.5" r="1.3" fill="#fff"/><circle cx="11" cy="10.5" r="1.3" fill="#fff"/></svg>
  </div>
</header>

<!-- Hero -->
<div class="photo hero-photo" role="img" aria-label="Child painting a craft project at a table with brushes and paint"></div>
<svg class="abs" style="left:0;top:568px" width="1200" height="40" viewBox="0 0 1200 40" preserveAspectRatio="none">
  <path d="M0 22 L60 16 L120 24 L200 14 L280 22 L360 12 L440 20 L520 10 L600 19 L680 11 L760 21 L840 13 L920 22 L1000 12 L1080 20 L1140 14 L1200 18 L1200 40 L0 40Z" fill="#fff"/>
</svg>
<div class="abs hero-frame">
  <h1>CRAFT IN THE COMFORT OF YOUR OWN HOME</h1>
  <p>At vero eos et accusamus et iusto odio dignissimos ducimus qui blanditiis praesentium voluptatum deleniti atque corrupti quos dolores et quas molestias excepturi sint occaecati</p>
  <div class="play"><i></i>PLAY VIDEO</div>
</div>

<!-- About -->
<h2 class="abs heading" style="left:115px;top:738px;font-size:32px">ABOUT US</h2>
<div class="brush" style="left:117px;top:793px;width:136px"></div>
<p class="abs about-text">Sed ut perspiciatis unde omnis iste natus error sit volupaccusantium doloremque laudantium, totam rem aperiam, eaque ipsa quae ab illo inventore veritatis et quasi architecto beatae vitae dicta suexplicabo. Nemo enim ipsam voluptatem quia voluptas sit aspernatur aut odit aut fugit, sed quia consequuntur magni dolores eos qui ravoluptatem sequi nesciunt. Neque porro quisquam est, qui dolorem ipsum quia dolor sit amet, consectetur, adipisci velit, sed quia non numqueius modi tempora incidunt ut labore et dolore</p>
<div class="btn" style="left:115px;top:1055px;width:156px;height:45px">LEARN MORE <span class="dot">›</span></div>
<div class="abs" style="left:660px;top:743px;width:425px;height:314px;border:5px solid var(--orange)"></div>
<div class="photo" style="left:639px;top:765px;width:426px;height:315px;background:linear-gradient(135deg,#d8c9b6,#b79a7c 50%,#e5ddd2)" role="img" aria-label="Two people assembling a white shelf on the floor"></div>

<!-- What we provide -->
<div class="abs" style="left:0;top:1215px;width:1200px;height:495px;background:var(--grey)"></div>
<svg class="abs" style="left:0;top:1200px" width="1200" height="30" viewBox="0 0 1200 30" preserveAspectRatio="none"><path d="M0 22 L100 14 L220 20 L340 10 L460 18 L600 8 L740 17 L880 9 L1000 18 L1120 11 L1200 16 L1200 30 L0 30Z" fill="var(--grey)"/></svg>
<svg class="abs" style="left:0;top:1690px" width="1200" height="30" viewBox="0 0 1200 30" preserveAspectRatio="none"><path d="M0 0 L1200 0 L1200 12 L1090 20 L960 10 L820 19 L680 9 L540 18 L400 10 L260 19 L120 11 L0 18Z" fill="var(--grey)"/></svg>
<h2 class="abs heading" style="left:0;width:1200px;text-align:center;top:1274px;font-size:32px">WHAT WE PROVIDE</h2>
<div class="brush" style="left:532px;top:1328px;width:136px"></div>
<div class="provide-card" style="left:108px" role="img" aria-label="Potter working at a pottery workstation">
  <div style="position:absolute;inset:0;background:linear-gradient(160deg,#cfc2ae,#7d6a55)"></div>
  <div class="label">WORKSTATIONS</div>
</div>
<div class="provide-card" style="left:442px" role="img" aria-label="Person painting with brushes and paint tubes">
  <div style="position:absolute;inset:0;background:linear-gradient(160deg,#dfe3e8,#9aa6b3 60%,#c95b3e)"></div>
  <div class="label">EQUIPMENT</div>
</div>
<div class="provide-card" style="left:776px" role="img" aria-label="Hands shaping clay">
  <div style="position:absolute;inset:0;background:linear-gradient(160deg,#e7c6c0,#b68b7e)"></div>
  <div class="label">TOOLS &amp; SUPPLIES</div>
</div>
<div class="arrow" style="left:31px;top:1478px"><svg width="10" height="14"><path d="M8 1 2 7l6 6" fill="none" stroke="#222" stroke-width="2"/></svg></div>
<div class="arrow" style="left:1131px;top:1478px"><svg width="10" height="14"><path d="M2 1l6 6-6 6" fill="none" stroke="#222" stroke-width="2"/></svg></div>

<!-- Bench activities -->
<div class="abs" style="left:474px;top:1914px;width:601px;height:358px;background:var(--orange-soft);border-radius:18px"></div>
<div class="photo" style="left:126px;top:1802px;width:447px;height:341px;border-radius:14px;background:linear-gradient(135deg,#3b2b20,#8a5f3e 50%,#3f6c78)" role="img" aria-label="Hand painting a vase on a pottery wheel"></div>
<h2 class="abs" style="left:604px;top:1950px;font:800 32px Rubik,sans-serif;color:#fff">BENCH ACTIVITIES</h2>
<p class="abs" style="left:604px;top:2036px;width:450px;font-size:13.5px;line-height:25.8px;color:#fff">Sed ut perspiciatis unde omnis iste natus error sitvolupaccusantium doloremque laudantium, totam rem aperiam, eaque ipsa quae ab illo inventore veritatis et quasi architecto beatae vitae dictasuexplicabo. Nemo enim ipsam voluptatem quia voluptas sit aspernatur aut odit aut fugit, sed quia consequuntur magni dolores</p>
<div class="btn" style="left:605px;top:2183px;width:155px;height:44px">LEARN MORE <span class="dot">›</span></div>

<!-- Features band -->
<div class="abs" style="left:0;top:2380px;width:1200px;height:267px;background:var(--purple)"></div>
<div class="feature" style="left:117px">
  <svg width="50" height="46" viewBox="0 0 50 46"><path d="M6 30h10l10 6 14-8M6 40h12l12 4 16-10" fill="none" stroke="#fff" stroke-width="3"/><rect x="20" y="4" width="20" height="18" fill="#fff"/></svg>
  <h3>CONVENIENT CRAFTING</h3><div class="line"></div>
  <p>Lorem ipsum dolor sit amet, consectetur adipiscing elit, sed do eiusmod tempor incidid</p>
</div>
<div class="feature" style="left:362px">
  <svg width="50" height="46" viewBox="0 0 50 46"><path d="M25 3 45 13 25 23 5 13Z" fill="#fff"/><path d="M5 22l20 10 20-10M5 31l20 10 20-10" fill="none" stroke="#fff" stroke-width="4"/></svg>
  <h3>CURATED MATERIALS</h3><div class="line"></div>
  <p>Lorem ipsum dolor sit amet, consectetur adipiscing elit, sed do eiusmod tempor incidid</p>
</div>
<div class="feature" style="left:608px">
  <svg width="50" height="46" viewBox="0 0 50 46"><path d="M12 3h18l9 9v31H12Z" fill="#fff"/><path d="M17 20h16M17 26h16M17 32h16M17 38h10" stroke="var(--purple)" stroke-width="2"/></svg>
  <h3>EASY-TO-FOLLOW INSTRUCTIONS</h3><div class="line"></div>
  <p>Lorem ipsum dolor sit amet, consectetur adipiscing elit, sed do eiusmod tempor incidid</p>
</div>
<div class="feature" style="left:853px">
  <svg width="50" height="46" viewBox="0 0 50 46"><circle cx="25" cy="23" r="11" fill="none" stroke="#fff" stroke-width="3"/><path d="M25 4v8M25 34v8M6 23h8M36 23h8M12 10l5 5M33 31l5 5M38 10l-5 5M12 36l5-5" stroke="#fff" stroke-width="3"/></svg>
  <h3>REACH OUT TO US</h3><div class="line"></div>
  <p>Lorem ipsum dolor sit amet, consectetur adipiscing elit, sed do eiusmod tempor incidid</p>
</div>

<!-- Blog -->
<div class="abs" style="left:111px;top:2737px;width:978px;height:613px;border:1px solid #ddd"></div>
<h2 class="abs heading" style="left:0;width:1200px;text-align:center;top:2773px;font-size:32px">LATEST BLOG</h2>
<div class="brush" style="left:520px;top:2828px;width:136px"></div>
<article class="blog-post" style="left:172px">
  <div class="photo" style="position:relative;width:420px;height:269px;background:linear-gradient(135deg,#3a3330,#8f7a68 55%,#d8cfc6)" role="img" aria-label="Potter shaping a bowl"></div>
  <h4>LOREM IPSUM DOLOR SIT AMET, CONSECTETUR<br>ADIPISCING ELIT, SED DO EIUSMOD</h4>
  <div class="meta"><b>▣</b>&nbsp; August 05, 2021 &nbsp;&nbsp;|&nbsp;&nbsp; <b>●</b>&nbsp; Bench Team</div>
  <p>Sed ut perspiciatis unde omnis iste natus error sit voluptatem<br>accusantium doloremque laudantium, totam</p>
</article>
<article class="blog-post" style="left:609px">
  <div class="photo" style="position:relative;width:420px;height:269px;background:linear-gradient(135deg,#2e2622,#7a5f48 50%,#c7a989)" role="img" aria-label="Clay vase on a pottery wheel"></div>
  <h4>LOREM IPSUM DOLOR SIT AMET, CONSECTETUR<br>ADIPISCING ELIT, SED DO EIUSMOD</h4>
  <div class="meta"><b>▣</b>&nbsp; July 05, 2021 &nbsp;&nbsp;|&nbsp;&nbsp; <b>●</b>&nbsp; Bench Team</div>
  <p>Sed ut perspiciatis unde omnis iste natus error sit voluptatem<br>accusantium doloremque laudantium, totam</p>
</article>

<!-- Team -->
<h2 class="abs heading" style="left:0;width:1200px;text-align:center;top:3417px;font-size:32px">OUR TEAM</h2>
<div class="brush" style="left:520px;top:3470px;width:136px"></div>
<div class="member" style="left:103px"><div class="face" role="img" aria-label="Team member portrait"></div><h5>ROWAN HALE</h5><div class="socials" style="left:56px;top:237px"><i></i><i></i><i></i><i></i></div></div>
<div class="member" style="left:355px"><div class="face" role="img" aria-label="Team member portrait"></div><h5>ROWAN HALE</h5><div class="socials" style="left:56px;top:237px"><i></i><i></i><i></i><i></i></div></div>
<div class="member" style="left:607px"><div class="face" role="img" aria-label="Team member portrait"></div><h5>ROWAN HALE</h5><div class="socials" style="left:56px;top:237px"><i></i><i></i><i></i><i></i></div></div>
<div class="member" style="left:858px"><div class="face" role="img" aria-label="Team member portrait"></div><h5>ROWAN HALE</h5><div class="socials" style="left:56px;top:237px"><i></i><i></i><i></i><i></i></div></div>

<!-- Get in touch -->
<div class="abs contact-band"></div>
<h2 class="abs" style="left:0;width:1180px;text-align:center;top:3925px;font:800 32px Rubik,sans-serif;color:#fff">GET IN TOUCH</h2>
<div class="brush" style="left:520px;top:3980px;width:136px;background:#fff"></div>
<div class="field" style="left:188px;top:4035px;width:384px;height:44px">Name</div>
<div class="field" style="left:188px;top:4095px;width:384px;height:44px">Email address</div>
<div class="field" style="left:188px;top:4155px;width:384px;height:44px">Phone No</div>
<div class="field" style="left:188px;top:4215px;width:384px;height:44px">Address</div>
<div class="field" style="left:583px;top:4035px;width:429px;height:158px">Message</div>
<p class="abs" style="left:584px;top:4215px;width:260px;font-size:11.5px;line-height:23px;color:#fff">This Form can only be sent with consent<br>to the privacy policy &nbsp;&nbsp;<span style="display:inline-block;width:15px;height:15px;border:1px solid #fff;vertical-align:middle"></span>&nbsp;&nbsp; I Agree</p>
<div class="btn" style="left:868px;top:4215px;width:144px;height:43px">SUBMIT NOW</div>

<!-- Footer -->
<footer class="abs site-footer"></footer>
<div class="abs" style="left:100px;top:4458px;width:180px;text-align:center;font:700 19px Rubik,sans-serif;color:#fff">MAPLE BENCH</div>
<div class="socials" style="left:116px;top:4505px;gap:6px"><i style="width:32px;height:32px;background:var(--orange);border:0"></i><i style="width:32px;height:32px;background:var(--orange);border:0"></i><i style="width:32px;height:32px;background:var(--orange);border:0"></i><i style="width:32px;height:32px;background:var(--orange);border:0"></i></div>
<div class="vline" style="left:336px"></div>
<div class="vline" style="left:558px"></div>
<div class="vline" style="left:814px"></div>

<div class="col-title" style="left:382px;top:4412px;position:absolute;font:700 13px Roboto,sans-serif;color:#fff">QUICK LINKS<span style="position:absolute;left:0;top:26px;width:26px;height:2px;background:#fff"></span></div>
<div class="f-list" style="left:382px;top:4460px"><div>Home</div><div>About Us</div><div>Bench activities</div><div>Bench events</div><div>Contact Us</div></div>

<div style="left:603px;top:4412px;position:absolute;font:700 13px Roboto,sans-serif;color:#fff">CONTACT US<span style="position:absolute;left:0;top:26px;width:26px;height:2px;background:#fff"></span></div>
<div class="c-item" style="top:4455px"><span class="ic"><svg width="10" height="14"><path d="M5 13S1 8 1 5a4 4 0 018 0c0 3-4 8-4 8z" fill="#fff"/></svg></span><span>23, Lorem Ipsum Dolr<br>United Kingdom</span></div>
<div class="c-item" style="top:4510px"><span class="ic"><svg width="12" height="12"><path d="M2 1l3 0 1 3-2 1a7 7 0 003 3l1-2 3 1v3C5 11 1 7 2 1z" fill="#fff"/></svg></span><span>1 555 010 010<br>1 555 020 020</span></div>
<div class="c-item" style="top:4565px"><span class="ic"><svg width="14" height="10"><rect x="0.5" y="0.5" width="13" height="9" fill="#fff"/><path d="M1 1l6 5 6-5" fill="none" stroke="var(--purple)"/></svg></span><span style="line-height:28px">info@maplebench.com</span></div>

<div style="left:870px;top:4412px;position:absolute;font:700 13px Roboto,sans-serif;color:#fff">OPERATING HOURS<span style="position:absolute;left:0;top:26px;width:26px;height:2px;background:#fff"></span></div>
<div class="f-list" style="left:870px;top:4460px"><div>Mon &nbsp;&nbsp;: &nbsp; 9.00 AM - 5.00 PM</div><div>Tue &nbsp;&nbsp;&nbsp;&nbsp;: &nbsp; 9.00 AM - 5.00 PM</div><div>Wed &nbsp;&nbsp;: &nbsp; 9.00 AM - 5.00 PM</div><div>Thu &nbsp;&nbsp;&nbsp;&nbsp;: &nbsp; 9.00 AM - 5.00 PM</div><div>Fri &nbsp;&nbsp;&nbsp;&nbsp;&nbsp;&nbsp;: &nbsp; 9.00 AM - 5.00 PM</div><div>Sat - Sun &nbsp;: &nbsp; Closed</div></div>

<div class="abs" style="left:105px;top:4665px;width:990px;height:1px;background:rgba(255,255,255,.35)"></div>
<p class="abs" style="left:0;width:1200px;text-align:center;top:4692px;font-size:13px;color:#fff">© 2021 The Maple Bench. All Rights Reserved</p>

</body>
</html>
```